Flyer für Verkauf von Radondetektoren
Zielgruppe
Ich verkaufe Radondetektoren zur Messung von Radon in Innenräumen. Zielgruppe sind Privatpersonen, Firmen, Genossenschaften und andere Hauseigentümer.
Aufgabenstellung
Ich brauche das Design für meine Messanleitung.
Kreativ - modern - weniger kann mehr sein
Struktur ist wichtigt, es soll also einfach sein zu lesen und zu verstehen, was gemacht werden soll. Können Bulletpoints, Icons mit eingebracht werden.
Wichtig ist auch, dass die beiden Logos 'Luftprüfer.de' und TESTOVAL' auf der Messanleitung vorhanden sind. Wobei 'Luftprüfer.de' das Hauptlogo ist.
DIN format dachte ich A4 beidseitig (Text müsste also auf diese Grösse angepasst werden).
Kann natürlich auch Flyer-Format sein oder andere Vorschläge!
Bildmaterial gibt es auf unsere Homepage https://luftprüfer.de und https://luftkontroll.se . Diese haben wir bereits gekauft und können verwendet werden. Ich lade sie den bei Bedarf hoch. Es können natürlich auch andere Vorschläge kommen.

```html
<!DOCTYPE html>
<html lang="de">
<head>
<meta charset="utf-8">
<title>Messanleitung – Luftprüfer.de</title>
<link href="https://fonts.googleapis.com/css2?family=Figtree:wght@400;500;600&display=swap" rel="stylesheet">
<style>
  :root {
    --ink: #1b1b1b;
    --accent: #dc9405;
    --brand-blue: #1f4e9a;
    --paper: #ffffff;
  }
  * { margin: 0; padding: 0; box-sizing: border-box; }
  html, body { width: 848px; height: 1200px; overflow: hidden; background: var(--paper); }
  body { font-family: "Figtree", Arial, sans-serif; color: var(--ink); font-size: 12.4px; line-height: 15.4px; }
  .page { position: relative; width: 848px; height: 1200px; }

  .brand-bar { position: absolute; top: 29px; right: 36px; display: flex; align-items: center; gap: 26px; }
  .brand-main { display: flex; align-items: center; gap: 6px; }
  .brand-dot { width: 16px; height: 16px; border-radius: 50%; background: var(--accent); }
  .brand-main .name { font-size: 16.5px; font-weight: 500; line-height: 17px; }
  .brand-main .tagline { font-size: 6.6px; letter-spacing: .3px; color: var(--accent); line-height: 8px; }
  .brand-partner { font-size: 18px; font-weight: 500; color: var(--brand-blue); }

  .block { position: absolute; left: 111px; width: 630px; }
  .subhead { font-weight: 500; }
  .step-title { font-size: 12.4px; font-weight: 400; padding-bottom: 2px; border-bottom: 1.5px solid var(--accent); display: inline-block; }
  .label { color: var(--accent); }
  .bullets { list-style: none; hyphens: auto; -webkit-hyphens: auto; }
  .bullets li { position: relative; padding-left: 26px; margin-bottom: 7.6px; }
  .bullets li::before { content: "•"; position: absolute; left: 0; font-size: 9px; }
  .bullets .strong { font-weight: 500; }
  b { font-weight: 600; }

  .address { display: flex; align-items: center; gap: 15px; }
  .address svg { flex: none; }
  .address p { font-weight: 600; }

  .footer { position: absolute; left: 0; bottom: 0; width: 848px; height: 85px; background: var(--accent); color: #fff; text-align: center; font-size: 11px; line-height: 14px; padding-top: 31px; }
</style>
</head>
<body>
<div class="page">
  <header class="brand-bar">
    <div class="brand-main">
      <span class="brand-dot"></span>
      <div>
        <div class="name">Luftprüfer.de</div>
        <div class="tagline">LUFTQUALITÄT EINFACH GEPRÜFT</div>
      </div>
    </div>
    <div class="brand-partner">TESTOVAL</div>
  </header>

  <p class="block subhead" style="top:78px">Platzierung der Detektoren im Raum:</p>
  <ul class="block bullets" style="top:100px">
    <li>Platzieren Sie die Detektoren in einem Mindestabstand von 20 cm zu Wänden, 50 cm zu Abluftsventilen, sowie 1,50 m zu Fenstern, Außentüren, Zuluftsventilen und Heizkörpern.</li>
    <li>Stellen Sie die Detektoren nicht auf dem Boden, an starken Wärmequellen oder Luftströmen auf. Vermeiden Sie auch Räume mit hoher Luftfeuchtigkeit, wie zum Beispiel das Badezimmer.</li>
    <li>Die Detektoren können entweder stehend (auf einem Tisch, im Regal oder einer Schrankwand) oder hängend mitten im Raum (z.B. von einer Lampe) platziert werden.</li>
    <li>Stellen Sie die Detektoren während der gesamten Messdauer nicht um.</li>
    <li>Versuchen Sie nicht das Gehäuse der Detektoren zu öffnen und platzieren Sie diese immer außer Reichweite von Kindern.</li>
  </ul>

  <div class="block" style="top:298px"><h2 class="step-title">SCHRITT 3: RADONMESSUNG</h2></div>
  <p class="block" style="top:328px">Die Radonmessung beginnt, sobald Sie die radondichten Verpackungen öffnen.<br>Bitte halten Sie die Messdauer wie folgt ein:</p>

  <p class="block label" style="top:374px">Kurzzeitmessung:</p>
  <ul class="block bullets" style="top:397px">
    <li>Mindestmessdauer 10 Tage (bis hin zu 30 Tagen).</li>
    <li>Führen Sie die Messung vorzugsweise in der Heizperiode (1. Oktober – 30. April) durch.</li>
    <li>Kurzzeitmessungen werden oft beim Kauf oder Verkauf von Immobilien genutzt, um ein mögliches Gefähr&shy;dungspotential abschätzen zu können, oder wenn die Zeit nicht ausreicht, um eine Langzeitmessung durchzuführen.</li>
  </ul>

  <p class="block label" style="top:504px">Langzeitmessung:</p>
  <ul class="block bullets" style="top:527px">
    <li>Mindestmessdauer 3 Monate während der Heizperiode (1. Oktober – 30. April).</li>
    <li>Um einen Jahresmittelwert der Radonkonzentration in Innenräumen ermitteln zu können, halten Sie die Messdauer von 12 Monaten ein.</li>
    <li class="strong">Falls Ihr Arbeitsplatz in einem Radon-Vorsorgegebiet liegt und somit der Messpflicht unterliegt, muss die Messdauer von 12 Monaten eingehalten werden.</li>
  </ul>

  <div class="block" style="top:648px"><h2 class="step-title">SCHRITT 4: ABSCHLUSS DER RADONMESSUNG MIT ABSCHLIESSENDEM PRÜFBERICHT</h2></div>
  <p class="block" style="top:680px">Nach Ablauf der Messdauer, loggen Sie sich auf <b>https://kundenportal.testoval.se/de</b> in Ihrem Account ein. Vermerken Sie hier das Ende der Messung und senden Sie anschließend alle Radondetektoren ausreichend frankiert in einem Umschlag oder einem Karton <b>zeitnah</b> an unsere <span class="label">Rücksendeadresse:</span></p>

  <div class="block address" style="top:742px">
    <svg width="37" height="24" viewBox="0 0 37 24" aria-hidden="true">
      <rect x="1" y="1" width="35" height="22" rx="2" fill="none" stroke="#dc9405" stroke-width="1.6"/>
      <path d="M1.5 2 L18.5 14 L35.5 2" fill="none" stroke="#dc9405" stroke-width="1.6"/>
    </svg>
    <p>Luftprüfer.de<br>Lindenstraße 14 – 27580 Musterhafen – Deutschland</p>
  </div>

  <p class="block" style="top:788px">Sobald die Radondetektoren im Labor von Testoval eingetroffen sind, werden diese fachgerecht analysiert und die Ergebnisse der Radonmessung ausgewertet. Ein vollständiger Prüfbericht wird Ihnen innerhalb 36 Stunden nach Erhalt der Detektoren im Labor per E-Mail zugeschickt.</p>

  <p class="block label" style="top:849px">Weitere Hinweise:</p>
  <ul class="block bullets" style="top:872px">
    <li>Bitte beachten Sie, dass die Radonmessung innerhalb von 15 Monaten nach Kaufdatum abgeschlossen sein muss.</li>
    <li>Versuchen Sie nicht das Gehäuse der Detektoren zu öffnen und platzieren Sie diese immer außer Reichweite von Kindern.</li>
    <li>Während der gesamten Messdauer dürfen die Detektoren nicht an einem anderen Ort umplatziert werden.</li>
    <li>Durch die Anmeldung auf der Website <b>https://kundenportal.testoval.se/de</b> und die Eingabe der erforderlichen Daten bestätigt der/die Wohnungseigentümer*in/Messverantwortliche, dass er/sie die Messanleitung befolgt hat und die Detektoren gemäß den Anweisungen korrekt platziert wurden.</li>
  </ul>

  <div class="block" style="top:1048px">
    <p class="label">Datenschutz (GDPR), Impressum und AGBs:</p>
    <p>Mehr Information dazu finden Sie unter <b>www.luftprüfer.de</b></p>
  </div>

  <footer class="footer">
    Copyright © 2023 NORDLUFT Mätning AB - Alle Rechte vorbehalten<br>
    https://www.luftprüfer.de
  </footer>
</div>
</body>
</html>
```